Creative, fresh business card design for Ripplecraft Facades

We need a fresh, creative business card design for Ripplecraft Facades. We are the manufacturer of Ripplecraft Facades in Australia. Wall panels are 2400 x 1200mm panels made from MDF and feature 3D patterns on the face of the panel. The colours to be used are green, silver/grey and white RGB
Red 187
Green 207
Blue 65.

An idea is to possibly use a watermark of one of our designs as a background (like on the "Grids" design on the left hand side of page 2 of our brochure).

Target Market(s)

Interior designers, architects, builders and home renovators

Industry/Entity Type

Business

Contact Information for Business Card

Details to go on the card are:
Our logo (attached),
Slogan: "Decorative panels for interiors and exteriors",
Contact name,
Position,
Mobile phone number,
Business address,
Business phone,
Business fax,
Website and
Email address.

I have attached a few images of our panels and our brochure for reference.

The colours of the business card should feature our logo colours which are: RGB
Red 187
Green 207
Blue 65

Requirements
Must have
• Very modern fonts and design. Some of the designs shown especially the "Prisms" design which is a popular design.
Nice to have
• Creative but simple design. Very contemporary.
Should not have
• Anything ornate or old fashioned.

```html
<!DOCTYPE html>
<html lang="en">
<head>
<meta charset="utf-8">
<title>Ripplecraft Facades – Business Card</title>
<link rel="stylesheet" href="https://fonts.googleapis.com/css2?family=Arimo:wght@400;700&display=swap">
<style>
  :root {
    --brand-green: rgb(187, 207, 65);
    --ink-grey: #555a5e;
    --soft-grey: #8a8e91;
    --rule-grey: #d9dadb;
    --card-white: #ffffff;
    --backdrop: #eceae6;
  }
  * { margin: 0; padding: 0; box-sizing: border-box; }
  html, body {
    width: 1200px; height: 987px; overflow: hidden;
    background: var(--backdrop);
    font-family: "Arimo", Arial, sans-serif;
  }
  .canvas { position: relative; width: 1200px; height: 987px; }
  .card {
    position: absolute; left: 293px; width: 614px; height: 350px;
    background: var(--card-white);
    box-shadow: 0 2px 8px rgba(0,0,0,0.18);
    overflow: hidden;
  }
  .card--front { top: 131px; }
  .card--back { top: 506px; }

  .brand-lockup {
    position: absolute; left: 60px; top: 100px; width: 220px;
    text-align: center;
  }
  .brand-mark {
    width: 58px; height: 58px; margin: 0 auto 12px;
    background: var(--brand-green);
  }
  .brand-name {
    font-size: 24px; font-weight: 700; line-height: 1.15;
    color: var(--ink-grey);
  }
  .brand-slogan {
    margin-top: 8px; font-size: 12px; letter-spacing: 2px;
    color: var(--soft-grey); line-height: 1.3;
  }
  .divider {
    position: absolute; left: 306px; top: 86px; width: 1px; height: 223px;
    background: var(--rule-grey);
  }
  .contact { position: absolute; left: 334px; top: 86px; color: var(--ink-grey); }
  .contact-name {
    font-size: 23px; font-weight: 700; color: var(--brand-green);
    letter-spacing: 0.5px;
  }
  .contact-role { margin-top: 2px; font-size: 17px; color: var(--soft-grey); }
  .contact-address { margin-top: 16px; font-size: 17px; line-height: 23px; }
  .contact-list { list-style: none; margin-top: 9px; font-size: 17px; }
  .contact-list li { display: flex; align-items: center; height: 23.5px; }
  .contact-list svg { width: 16px; height: 16px; margin-right: 8px; fill: var(--brand-green); }

  .feature-photo {
    position: absolute; left: 0; top: 0; width: 279px; height: 100%;
    background: linear-gradient(160deg, #f3f3f1 0%, #c9c3b8 38%, #8a6a4c 62%, #4b3324 100%);
  }
  .panel-texture {
    position: absolute; left: 279px; top: 0; right: 0; height: 100%;
    background: radial-gradient(circle at 55% 45%, #f7f7f7 0%, #e4e4e4 60%, #cfcfcf 100%);
  }
  .back-lockup {
    position: absolute; left: 279px; right: 0; top: 105px; text-align: center;
  }
  .back-lockup .brand-mark { width: 66px; height: 66px; }
  .back-lockup .brand-name { font-size: 28px; color: var(--ink-grey); }
  .back-lockup .brand-slogan {
    font-size: 13px; font-weight: 700; letter-spacing: 2.5px; color: var(--ink-grey);
  }
</style>
</head>
<body>
<main class="canvas">
  <section class="card card--front" aria-label="Card front">
    <div class="brand-lockup">
      <div class="brand-mark"></div>
      <div class="brand-name">Ripplecraft<br>Facades</div>
      <div class="brand-slogan">decorative panels for<br>interiors &amp; landscapes</div>
    </div>
    <div class="divider"></div>
    <div class="contact">
      <div class="contact-name">DANIEL HARLOW</div>
      <div class="contact-role">CEO&amp;Founder</div>
      <div class="contact-address">1342 Wattle Grove Road<br>Geelong, Victoria 3220</div>
      <ul class="contact-list">
        <li><svg viewBox="0 0 16 16"><path d="M3 1h3l1.5 4-2 1.3a9 9 0 0 0 4.2 4.2L11 8.5l4 1.5v3a2 2 0 0 1-2 2A12 12 0 0 1 1 3a2 2 0 0 1 2-2z"/></svg>(555) 210-4837</li>
        <li><svg viewBox="0 0 16 16"><rect x="4" y="1" width="8" height="5"/><rect x="1" y="6" width="14" height="6" rx="1"/><rect x="4" y="10" width="8" height="5" fill="#fff" stroke="rgb(187,207,65)" stroke-width="1.5"/></svg>(555) 210-4838</li>
        <li><svg viewBox="0 0 16 16"><rect x="1" y="3" width="14" height="10"/><path d="M1 3l7 6 7-6" fill="none" stroke="#fff" stroke-width="1.4"/></svg>dharlow@ripplecraft.example</li>
        <li><svg viewBox="0 0 16 16"><circle cx="8" cy="8" r="7"/><path d="M1 8h14M8 1c-3 3-3 11 0 14M8 1c3 3 3 11 0 14" fill="none" stroke="#fff" stroke-width="1.1"/></svg>www.ripplecraft.example</li>
      </ul>
    </div>
  </section>

  <section class="card card--back" aria-label="Card back">
    <div class="feature-photo" role="img" aria-label="Photo of a bright office lobby with timber details, green lounge chairs and a sculpture"></div>
    <div class="panel-texture" role="img" aria-label="White 3D faceted wall panel texture"></div>
    <div class="back-lockup">
      <div class="brand-mark"></div>
      <div class="brand-name">Ripplecraft Facades</div>
      <div class="brand-slogan">decorative panels for<br>interiors &amp; landscapes</div>
    </div>
  </section>
</main>
</body>
</html>
```